Packaging and Insert Design for New Cocktail/Bar Set

We are launching a new product under our brand, Shaker Haven, and require a design for the product packaging (2 packages - an inner cylinder tube and an outer box), as well as an insert.

(Note for reference - "mixology" is the art of cocktail making).

Our product is a cocktail set which will be sold on the USA Amazon site.

Our logo has already been designed - please refer to the attached files. I've attached various vector files of our logo.

The cocktail set will be packaged in a cylinder tube box.
Please see uploaded files for an image of the cylinder, as well as dimensions.
Dimensions are 37.68cm x 28cm (when the print design is laid flat).
The physical tube will be 28cm high and have a diameter of 12cm.
See uploaded file 'Dimensions - Cylinder Box' for details.

The cylinder box will be enclosed in an outer white box for protection. The outer white box will be a very basic box (i.e. not high quality) we are using just to make storage of individual units easier (and to protect the cylinder tube). It is unlikely that the outer box will be retained by the buyer. It will have a very clean, simple design. It will have our logo on the front and a barcode on the back (at the bottom).
Dimensions of the outer box are 28.5cm high and 12.5cm wide (tall and rectangular in shape).
See uploaded file 'Dimensions - White Outer Box & Paper Card' for details.

So to confirm we have 2 packages - the internal cylinder tube will have full branding, and this will then be placed in the white outer box with a simple design (logo only plus barcode at the back).

We also require a small insert to be designed (9.1cm x 5.5cm). We will include the insert in the package. The insert will have our logo and will provide the buyer with our contact details. The buyer will register their email address with us, in order to quality for warranty and a free e-book.

We need to finalise the content for the product insert, as well as the additional information to be printed on the cylinder tube.

In terms of design for the inner cylinder tube, we are leaning towards a more simple design, with our logo displayed on the front of the box.
We are open to ideas/suggestions though.

We have also uploaded an image of the cocktail set components which will form part of the set.

Target Market(s)

Our target market will be cocktail making enthusiasts/hobbyists and professionals. This includes people who would like to but a cocktail set to use at home, as well as professional bartenders.

Industry/Entity Type

Product

Colors

Designer to choose colors to be used in the design.

Requirements
Must have
• Preference is for a clean, professional looking design.
• Internal cylinder tube - full branding, incorporating logo on the front. Possibly also either a slogan e.g. "The Art of Cocktail Making' or details of the product e.g. "Cocktail Making Set' or similar.
• Outer white box - very simple design with logo to be displayed on the front of the packaging.
Should not have
• The design should not be too busy/complex. Not too much going on.

```html
<!DOCTYPE html>
<html lang="en">
<head>
<meta charset="utf-8">
<title>Shaker Haven – Cylinder Tube Wrap</title>
<link rel="stylesheet" href="https://fonts.googleapis.com/css2?family=Gochi+Hand&family=Oswald:wght@400&display=swap">
<style>
  :root {
    --paper: #ffffff;
    --wrap: #000000;
    --bleed-line: #8b0000;
    --ink: #ffffff;
    --bubble: rgba(255, 255, 255, 0.12);
  }
  html, body {
    margin: 0;
    padding: 0;
    width: 1200px;
    height: 1176px;
    overflow: hidden;
    background: var(--paper);
  }
  .canvas {
    position: relative;
    width: 1200px;
    height: 1176px;
  }
  .artwork {
    position: absolute;
    inset: 0;
    width: 1200px;
    height: 1176px;
  }
  .slogan {
    position: absolute;
    right: 163px;
    top: 424px;
    margin: 0;
    font-family: "Gochi Hand", cursive;
    font-weight: 400;
    font-size: 20px;
    color: var(--ink);
    letter-spacing: 0.5px;
  }
  .contents {
    position: absolute;
    right: 165px;
    top: 488px;
    margin: 0;
    padding: 0;
    list-style: none;
    text-align: right;
    font-family: "Oswald", sans-serif;
    font-size: 14.5px;
    line-height: 30.3px;
    color: var(--ink);
    letter-spacing: 0.6px;
  }
  .contents li::before {
    content: "\2022";
    margin-right: 6px;
  }
  .brand-name {
    position: absolute;
    left: 0;
    width: 1200px;
    top: 818px;
    margin: 0;
    text-align: center;
    font-family: "Oswald", sans-serif;
    font-weight: 400;
    font-size: 46px;
    letter-spacing: 10px;
    color: var(--ink);
  }
</style>
</head>
<body>
<main class="canvas">
  <svg class="artwork" viewBox="0 0 1400 1372" preserveAspectRatio="none" aria-hidden="true">
    <defs>
      <clipPath id="wrap-area">
        <rect x="126" y="267" width="1147" height="838"/>
      </clipPath>
    </defs>
    <rect class="wrap-panel" x="126" y="267" width="1147" height="838" fill="var(--wrap)"/>
    <g class="bubbles" clip-path="url(#wrap-area)" fill="var(--bubble)">
      <ellipse cx="276" cy="472" rx="100" ry="137"/>
      <ellipse cx="276" cy="700" rx="78" ry="155" transform="rotate(14 276 700)"/>
      <ellipse cx="276" cy="913" rx="80" ry="117"/>
      <ellipse cx="700" cy="340" rx="187" ry="72"/>
      <ellipse cx="700" cy="482" rx="158" ry="72" transform="rotate(-12 700 482)"/>
      <ellipse cx="700" cy="625" rx="152" ry="70" transform="rotate(8 700 625)"/>
      <ellipse cx="700" cy="748" rx="132" ry="62" transform="rotate(-15 700 748)"/>
    </g>
    <rect class="safe-line" x="173" y="294" width="1054" height="784" fill="none" stroke="var(--bleed-line)" stroke-width="1"/>
  </svg>

  <p class="slogan">The art of Cocktail Making</p>

  <ul class="contents">
    <li>COBBLER SHAKER</li>
    <li>BAR SPOON</li>
    <li>JIGGER - 1OZ 2OZ"</li>
    <li>STRAINER 4"</li>
    <li>ICE TONGS SET</li>
    <li>POUR SPOUTS X4</li>
    <li>RECIPE CARDS</li>
  </ul>

  <p class="brand-name">SHAKER HAVEN</p>
</main>
</body>
</html>
```